Larvik GmbH needs a sensational homepage!

A draft of the performances and the logo were uploaded in the attachment. The homepage should be adapted to the colors of the logo. Either pictures, graphics or icons of the respective topic are to be used for the buttons. Social media Linkedin, Youtube, Instagram should not be missing. An imprint, contact form with telephone number and email address should be given on the home page. The page should definitely be designed to be responsive for all end devices. Texts as well as images and videos are inserted in the sub-menus or pages. Only the structure and a simple application should be given. We have already secured the domain www.larvik-demo.at.
We are a young, dynamic company with a high technical affinity. Ask for creative suggestions. If something is needed, please contact us.

Target Market(s)

Construction industry, client

Requirements
Must have
• see description
Should not have
• shouldn't be colorful and playful

```html
<!DOCTYPE html>
<html lang="en">
<head>
<meta charset="utf-8">
<title>Larvik GmbH – Home</title>
<link href="https://fonts.googleapis.com/css2?family=Lato:wght@400;700;900&display=swap" rel="stylesheet">
<style>
:root{
  --orange:#f0711c;
  --slate:#253a47;
  --card:#263b46;
  --blue:#26358a;
  --grey-bg:#ebebeb;
  --text:#3c3c3c;
  --white:#ffffff;
  --dot:#cfcfcf;
  --social:#444b52;
}
*{margin:0;padding:0;box-sizing:border-box}
html,body{width:1200px;height:3572px;overflow:hidden}
body{font-family:'Lato',sans-serif;color:var(--text);position:relative;background:var(--white)}
section,footer{position:absolute;left:0;width:1200px}
.center{position:absolute;left:0;width:1200px;text-align:center}
.btn{position:absolute;background:var(--orange);color:var(--white);display:flex;align-items:center;justify-content:center;font-weight:700;text-decoration:none}

/* hero */
.hero{top:0;height:714px;background:linear-gradient(160deg,#7d7f80 0%,#5b5e60 40%,#3e4247 75%,#5e6266 100%)}
.hero-photo{position:absolute;inset:0}
.logo{position:absolute;left:75px;top:49px;width:223px;height:65px;display:flex;align-items:center;justify-content:center;color:var(--white);font-size:46px;font-weight:400;letter-spacing:10px}
.nav{position:absolute;top:65px;left:420px;display:flex;height:32px;align-items:center;color:var(--white);font-size:16px;font-weight:700}
.nav a{color:inherit;text-decoration:none;padding:0 19px;height:32px;display:flex;align-items:center}
.nav a.active{background:var(--orange)}
.nav a:nth-child(n+2){margin-left:10px}
.hero-title{top:262px;font-size:112px;font-weight:900;color:var(--white);letter-spacing:-1px;line-height:140px}
.hero-sub{top:388px;font-size:32px;font-weight:700;color:var(--white);line-height:47px}

/* shared */
h2{font-size:43px;font-weight:700;color:var(--slate);line-height:56px}
.lead{font-size:14.5px;font-weight:700;color:var(--blue);line-height:28px}
.body-txt{font-size:14.5px;line-height:28.5px;color:var(--text)}

.welcome{top:714px;height:480px}

/* services */
.services{top:1194px;height:504px;background:linear-gradient(135deg,#1b2637 0%,#0e1b2e 45%,#14233a 70%,#2b3440 100%)}
.services h2{color:var(--white)}
.service{position:absolute;top:200px;width:270px;text-align:center}
.service-icon{display:block;margin:0 auto}
.service h3{color:var(--orange);font-size:21px;font-weight:700;line-height:28px;margin-top:22px}
.service p{color:var(--white);font-size:14px;line-height:28.5px;margin-top:8px}

.why{top:1698px;height:422px;background:var(--grey-bg)}

/* testimonials */
.testimonials{top:2120px;height:602px}
.t-card{position:absolute;top:195px;width:330px;height:253px;background:var(--card);color:var(--white);text-align:center;padding:0 24px}
.quote{display:block;margin:30px auto 0}
.t-card p{font-size:15px;line-height:27.8px;margin-top:18px}
.t-name{position:absolute;top:470px;width:330px;text-align:center;font-size:17px;font-weight:700;color:var(--slate)}
.stars{position:absolute;top:506px;width:330px;display:flex;justify-content:center;gap:3px}

/* contact */
.contact{top:2722px;height:567px;background:linear-gradient(120deg,#22303f 0%,#15222f 45%,#0e1723 100%)}
.contact h2{color:var(--white)}
.contact-line{top:131px;color:var(--white);font-size:15px;display:flex;justify-content:center;align-items:center;gap:10px}
.field{position:absolute;left:300px;width:602px;background:var(--white);font-size:13px;color:#333;padding:10px 14px}

/* footer */
.footer{top:3289px;height:283px;font-size:15px;line-height:26px;color:#333}
.social{position:absolute;top:72px;width:22px;height:22px;border-radius:4px;background:var(--social)}

.dots{position:absolute;left:1140px;display:flex;flex-direction:column;gap:18.5px}
.dots span{width:12px;height:12px;border-radius:50%;background:var(--dot)}
.dots.light span{background:var(--white)}
.dots span.on{background:var(--orange)}
</style>
</head>
<body>

<svg width="0" height="0" style="position:absolute">
  <defs>
    <path id="star" d="M8 0.8l2.2 4.6 5 .6-3.7 3.4 1 5L8 12 3.5 14.4l1-5L.8 6l5-.6z" fill="#f0711c"/>
    <g id="quote-mark" fill="#f0711c">
      <path d="M2 38V22C2 10 8 3 18 1l2 5c-5 2-8 6-8 11h8v21z"/>
      <path d="M26 38V22c0-12 6-19 16-21l2 5c-5 2-8 6-8 11h8v21z"/>
    </g>
  </defs>
</svg>

<section class="hero">
  <div class="hero-photo" role="img" aria-label="Workers in hard hats and safety harnesses assembling steel scaffolding"></div>
  <div class="logo">LARVIK</div>
  <nav class="nav">
    <a class="active" href="#">Home</a>
    <a href="#">Scaffolding</a>
    <a href="#">Rehabilitation Project Management</a>
    <a href="#">Screed &amp; insulation</a>
  </nav>
  <h1 class="center hero-title">Larvik</h1>
  <p class="center hero-sub">We are a young, dynamic company with a high<br>technical affinity in Upper Austria.</p>
</section>

<section class="welcome">
  <h2 class="center" style="top:58px">Welcome to Larvik</h2>
  <p class="center lead" style="top:129px">Class aptent taciti sociosqu ad litora torquent per conubia nostra, per inceptos himenaeos. Sed cursus turpis sed lectus interdum, sed<br>ullamcorper nunc malesuada. Sed nec est vel arcu sodales egestas sit amet vel nulla.</p>
  <p class="center body-txt" style="top:201px">Lorem ipsum dolor sit amet, consectetur adipiscing elit. Integer auctor feugiat libero vitae tincidunt. Ut varius malesuada ex at porta.<br>Quisque augue mauris, dignissim sed velit eget, finibus porta urna. Suspendisse eget tempor risus, et imperdiet nisi.<br>Proin rhoncus, tellus sagittis rutrum aliquam, est ipsum vestibulum leo, vel tempor orci lacus ut nunc. Vivamus aliquet lectus nisl, vitae<br>efficitur nisl dignissim quis.</p>
  <a class="btn" href="#" style="left:497px;top:347px;width:208px;height:56px;font-size:19px">Read More</a>
  <div class="dots" style="top:153px"><span class="on"></span><span></span><span></span><span></span><span></span></div>
</section>

<section class="services">
  <div role="img" aria-label="Scaffolding silhouetted against a dark evening sky" style="position:absolute;inset:0"></div>
  <h2 class="center" style="top:57px">Our Services</h2>
  <p class="center" style="top:130px;color:var(--white);font-size:16px;font-weight:700">Morbi id congue nibhhasellus maximus nisl ante, ut dictum felis.</p>

  <div class="service" style="left:105px">
    <svg class="service-icon" width="70" height="72" viewBox="0 0 70 72" fill="none" stroke="#fff" stroke-width="2.4" aria-label="Scaffolding icon" role="img">
      <rect x="3" y="3" width="64" height="8"/>
      <line x1="8" y1="11" x2="8" y2="66"/><line x1="62" y1="11" x2="62" y2="66"/>
      <line x1="8" y1="11" x2="62" y2="60"/><line x1="62" y1="11" x2="8" y2="60"/>
      <line x1="8" y1="36" x2="62" y2="36"/>
      <rect x="4" y="60" width="8" height="8"/><rect x="58" y="60" width="8" height="8"/>
    </svg>
    <h3>Scaffolding</h3>
    <p>Nullam ultrices placerat libero, in tristique<br>massa euismod eget. Suspendisse<br>semper sapien</p>
  </div>

  <div class="service" style="left:464px">
    <svg class="service-icon" width="70" height="72" viewBox="0 0 70 72" fill="none" stroke="#fff" stroke-width="2.4" aria-label="Project plan with gear icon" role="img">
      <rect x="6" y="4" width="46" height="58" rx="2"/>
      <line x1="6" y1="14" x2="52" y2="14"/>
      <line x1="13" y1="24" x2="34" y2="24"/><line x1="13" y1="32" x2="30" y2="32"/>
      <line x1="13" y1="40" x2="28" y2="40"/><line x1="13" y1="48" x2="28" y2="48"/>
      <circle cx="50" cy="50" r="12" fill="#0f1e31"/><circle cx="50" cy="50" r="5"/>
      <path d="M50 34v5M50 61v5M34 50h5M61 50h5M39 39l3.5 3.5M57.5 57.5L61 61M61 39l-3.5 3.5M42.5 57.5L39 61"/>
    </svg>
    <h3>Rehabilitation Project<br>Management</h3>
    <p>Nullam ultrices placerat libero, in tristique<br>massa euismod eget. Suspendisse<br>semper sapien</p>
  </div>

  <div class="service" style="left:822px">
    <svg class="service-icon" width="70" height="72" viewBox="0 0 70 72" fill="none" stroke="#fff" stroke-width="2.4" aria-label="House with floor heating icon" role="img">
      <circle cx="16" cy="12" r="5"/>
      <path d="M16 2v3M16 19v3M6 12h3M23 12h3"/>
      <path d="M3 36L35 8l32 28"/>
      <path d="M11 30v36h48V30"/>
      <path d="M20 62c-4-5 4-9 0-14s4-9 0-14M30 62c-4-5 4-9 0-14s4-9 0-14M40 62c-4-5 4-9 0-14s4-9 0-14M50 62c-4-5 4-9 0-14s4-9 0-14"/>
    </svg>
    <h3>Screed &amp; Insulation</h3>
    <p>Nullam ultrices placerat libero, in tristique<br>massa euismod eget. Suspendisse<br>semper sapien</p>
  </div>
  <div class="dots light" style="top:182px"><span></span><span class="on"></span><span></span><span></span><span></span></div>
</section>

<section class="why">
  <h2 class="center" style="top:65px">Why Larvik ?</h2>
  <p class="center body-txt" style="top:138px">Lorem ipsum dolor sit amet, consectetur adipiscing elit. Integer auctor feugiat libero vitae tincidunt. Ut varius malesuada ex at porta.<br>Quisque augue mauris, dignissim sed velit eget, finibus porta urna. Suspendisse eget tempor risus, et imperdiet nisi.<br>Proin rhoncus, tellus sagittis rutrum aliquam, est ipsum vestibulum leo, vel tempor orci lacus ut nunc. Vivamus aliquet lectus nisl,<br>vitae efficitur nisl dignissim quis.</p>
  <a class="btn" href="#" style="left:497px;top:293px;width:208px;height:56px;font-size:19px">Read More</a>
  <div class="dots" style="top:98px"><span></span><span></span><span class="on"></span><span></span><span></span></div>
</section>

<section class="testimonials">
  <h2 class="center" style="top:58px">Testimonials</h2>
  <p class="center" style="top:133px;font-size:14.5px;font-weight:700;color:#2e2e2e">Lorem ipsum dolor sit amet, consectetur adipiscing elit. Integer auctor feugiat libero vitae tincidunt.</p>

  <div class="t-card" style="left:75px"><svg class="quote" width="44" height="38"><use href="#quote-mark"/></svg><p>“ Lorem ipsum dolor sit amet, consectetur adipiscing elit. Integer auctor feugiat libero vitae tincidunt. Ut varius malesuada ex at porta maximus nisl ante, ut dictum felis luctus..”</p></div>
  <div class="t-card" style="left:436px"><svg class="quote" width="44" height="38"><use href="#quote-mark"/></svg><p>“ Lorem ipsum dolor sit amet, consectetur adipiscing elit. Integer auctor feugiat libero vitae tincidunt. Ut varius malesuada ex at porta maximus nisl ante, ut dictum felis luctus..”</p></div>
  <div class="t-card" style="left:796px"><svg class="quote" width="44" height="38"><use href="#quote-mark"/></svg><p>“ Lorem ipsum dolor sit amet, consectetur adipiscing elit. Integer auctor feugiat libero vitae tincidunt. Ut varius malesuada ex at porta maximus nisl ante, ut dictum felis luctus..”</p></div>

  <div class="t-name" style="left:75px">Name Heading</div>
  <div class="t-name" style="left:436px">Name Heading</div>
  <div class="t-name" style="left:796px">Name Heading</div>

  <div class="stars" style="left:75px"><svg width="16" height="15"><use href="#star"/></svg><svg width="16" height="15"><use href="#star"/></svg><svg width="16" height="15"><use href="#star"/></svg><svg width="16" height="15"><use href="#star"/></svg><svg width="16" height="15"><use href="#star"/></svg></div>
  <div class="stars" style="left:436px"><svg width="16" height="15"><use href="#star"/></svg><svg width="16" height="15"><use href="#star"/></svg><svg width="16" height="15"><use href="#star"/></svg><svg width="16" height="15"><use href="#star"/></svg><svg width="16" height="15"><use href="#star"/></svg></div>
  <div class="stars" style="left:796px"><svg width="16" height="15"><use href="#star"/></svg><svg width="16" height="15"><use href="#star"/></svg><svg width="16" height="15"><use href="#star"/></svg><svg width="16" height="15"><use href="#star"/></svg><svg width="16" height="15"><use href="#star"/></svg></div>

  <div class="dots" style="top:255px"><span></span><span></span><span class="on"></span><span></span><span></span></div>
</section>

<section class="contact">
  <div role="img" aria-label="Hands working over documents and a laptop on a dark desk" style="position:absolute;inset:0"></div>
  <h2 class="center" style="top:52px">Contact Us</h2>
  <div class="center contact-line">
    <svg width="15" height="15" viewBox="0 0 24 24"><path fill="#fff" d="M6.6 10.8a15 15 0 0 0 6.6 6.6l2.2-2.2c.3-.3.7-.4 1-.2 1.1.4 2.3.6 3.6.6.6 0 1 .4 1 1V20c0 .6-.4 1-1 1A17 17 0 0 1 3 4c0-.6.4-1 1-1h3.5c.6 0 1 .4 1 1 0 1.3.2 2.5.6 3.6.1.3 0 .7-.2 1z"/></svg>
    <span>1-800-555-0142 &nbsp;|</span>
    <svg width="16" height="13" viewBox="0 0 16 13" style="margin-left:6px"><rect width="16" height="13" rx="1" fill="#fff"/><path d="M1 1.5l7 5.5 7-5.5" stroke="#15222f" stroke-width="1.4" fill="none"/></svg>
    <span style="margin-left:6px">info@larvik-demo.at</span>
  </div>
  <div class="field" style="top:179px;height:36px">Name</div>
  <div class="field" style="top:226px;height:38px">Email Address</div>
  <div class="field" style="top:273px;height:38px">Phone</div>
  <div class="field" style="top:320px;height:123px">Message</div>
  <a class="btn" href="#" style="left:524px;top:465px;width:153px;height:38px;font-size:18px">Submit</a>
  <div class="dots light" style="top:222px"><span></span><span></span><span></span><span class="on"></span><span></span></div>
</section>

<footer class="footer">
  <p style="position:absolute;left:343px;top:57px;width:240px">Nullam ultrices placerat libero, in tristique massa euismod eget. Suspendisse semper sapien eget enim sed mauris.</p>
  <p style="position:absolute;left:646px;top:57px">48 Birch Avenue<br>Springfield, CA 94100</p>
  <p style="position:absolute;left:646px;top:121px;display:flex;align-items:center;gap:20px">
    <svg width="13" height="13" viewBox="0 0 24 24"><path fill="#333" d="M6.6 10.8a15 15 0 0 0 6.6 6.6l2.2-2.2c.3-.3.7-.4 1-.2 1.1.4 2.3.6 3.6.6.6 0 1 .4 1 1V20c0 .6-.4 1-1 1A17 17 0 0 1 3 4c0-.6.4-1 1-1h3.5c.6 0 1 .4 1 1 0 1.3.2 2.5.6 3.6.1.3 0 .7-.2 1z"/></svg>123-555-0190</p>
  <a class="social" href="#" role="img" aria-label="Professional network profile" style="left:912px"></a>
  <a class="social" href="#" role="img" aria-label="Video channel" style="left:946px"></a>
  <a class="social" href="#" role="img" aria-label="Photo feed" style="left:980px"></a>
  <p class="center" style="top:206px;font-size:13px">Copyright © 2021 Larvik GmbH All rights reserved.</p>
</footer>

</body>
</html>
```